Corinnehabbard.com

1. Conceptualization and designing of the site Homepage. The Homepage design will be completely customized and based on your design instructions (i.e. preferred colors, links to reference sites that you want us to take reference from if any etc) and the recently completed logo design.
2. Upon homepage design approval, based on it we will be creating the layout for the other 4 site inner pages (i.e. About page, Contact page, Services page, and Insights (publications, media).
3. Once all the inner page designs are approved, we will get the designs built (will make sure that the site is completely Responsive - works on all devices) within your provided WIX account.
4. We will add the static text and images provided by you to the Home page, About page, Contact page, and the Services page. For the 2 Insights sub-pages, we will add 1-2 sample Publications and Media entries.
once you confirm the total number of required entries for the 2 sub-pages, I will accordingly quote you on the same
5. Integration of a Contact form on the Contact page that will email the filled in details to your mail id.

```html
<!DOCTYPE html>
<html lang="en">
<head>
<meta charset="utf-8">
<title>Corinne Habbard Consulting</title>
<link href="https://fonts.googleapis.com/css2?family=Montserrat:wght@400;500;600;700&display=swap" rel="stylesheet">
<style>
:root{
  --blue:#0a9be0;
  --green:#14902f;
  --orange:#f39200;
  --red:#e30613;
  --ink:#1d1d1b;
  --paper:#f4f4f4;
  --white:#ffffff;
  --line:#9a9a9a;
}
*{margin:0;padding:0;box-sizing:border-box}
html,body{width:1200px;height:3281px;overflow:hidden;background:var(--white)}
body{position:relative;font-family:'Montserrat',sans-serif;color:var(--ink)}
.abs{position:absolute}
a{color:inherit;text-decoration:none}

/* hero */
.hero{left:74px;top:0;width:1049px;height:587px;background:var(--paper);overflow:hidden}
.hero svg{position:absolute;left:0;top:0}
.brand{display:flex;flex-direction:column;align-items:center;text-align:center;font-weight:600;letter-spacing:.5px;white-space:nowrap}
.brand .mark{width:48px;height:48px;border-radius:50%;border:3px solid currentColor;margin-bottom:10px}
.brand .name{font-size:14.5px;line-height:1.1}
.brand .sub{font-size:10px;letter-spacing:3px;margin-top:2px}
.hero .brand{left:44px;top:32px;width:190px;color:var(--blue)}
.nav{top:68px;font-size:14.5px;font-weight:500;color:#222}
.nav.active{color:var(--blue)}
.hero-title{left:117px;top:170px;font-size:24px;font-weight:500;color:var(--blue);letter-spacing:.3px;white-space:nowrap}
.hero-title b{color:var(--green);font-weight:600}
.hero-text{left:117px;top:211px;width:440px;font-size:13.5px;line-height:34px;font-weight:500;white-space:nowrap}
.hero-mark{left:665px;top:133px;width:242px;height:242px;border-radius:50%;border:4px solid var(--ink);background:var(--white);display:flex;align-items:center;justify-content:center;text-align:center;font-size:20px;font-weight:600;color:var(--blue);line-height:1.3}

/* section titles */
.section-title{left:0;width:1200px;text-align:center;font-size:32px;font-weight:500;color:var(--blue);letter-spacing:.5px}
.section-title b{color:var(--green);font-weight:600}

/* buttons */
.btn{display:flex;align-items:center;justify-content:center;gap:10px;height:49px;border-radius:25px;background:var(--blue);color:var(--white);font-size:16.5px;font-weight:600;letter-spacing:.3px;white-space:nowrap}
.btn.light{background:var(--white);color:var(--blue)}

/* services */
.service{top:775px;width:256px;height:369px;border-radius:4px;color:var(--white);text-align:center}
.service .icon{position:absolute;left:87px;top:44px;width:82px;height:82px;border-radius:50%;border:2px solid var(--white)}
.service .icon svg{position:absolute;left:19px;top:19px}
.service h3{position:absolute;top:156px;width:100%;font-size:16.5px;font-weight:600;letter-spacing:.3px}
.service p{position:absolute;top:192px;left:0;right:0;font-size:13.5px;line-height:28px;font-weight:600;white-space:nowrap}
.service .go{position:absolute;left:114px;top:294px;width:28px;height:28px;border-radius:50%;background:var(--white)}
.s-blue{left:74px;background:var(--blue)}
.s-green{left:339px;background:var(--green)}
.s-orange{left:605px;background:var(--orange)}
.s-red{left:870px;background:var(--red)}

/* about */
.about{left:74px;top:1345px;width:1049px;height:527px;background:linear-gradient(135deg,#0b8fd6,#15a7ea 50%,#0a92d9);overflow:hidden}
.about-photo{left:109px;top:129px;width:254px;height:254px;border-radius:50%;background:radial-gradient(circle at 60% 35%,#c9d8e6,#6b7c8c 60%,#3a3e45)}
.about h2{left:507px;top:70px;font-size:32px;font-weight:600;color:var(--white);letter-spacing:.5px}
.about p{left:507px;top:126px;width:500px;font-size:13.5px;line-height:34px;font-weight:600;color:var(--white);white-space:nowrap}

/* insights */
.insight{top:2045px;width:342px;height:243px;background:var(--white);box-shadow:0 0 6px rgba(0,0,0,.16);border-radius:3px}
.insight .social{position:absolute;left:32px;top:36px;width:56px;height:56px;border-radius:50%;border:1px solid #555;display:flex;align-items:center;justify-content:center;font-size:9px;font-weight:600;color:#333}
.insight h4{position:absolute;left:118px;top:38px;font-size:16.5px;font-weight:500;color:var(--blue);letter-spacing:.3px}
.insight time{position:absolute;left:120px;top:73px;font-size:12.5px;font-weight:600}
.insight p{position:absolute;left:33px;top:110px;width:300px;font-size:13.5px;line-height:34.5px;font-weight:500;white-space:nowrap}

/* contact */
.field{height:42px;border-bottom:2px solid var(--line);font-size:17.5px;font-weight:500;letter-spacing:.2px}
.field svg{position:absolute;right:0;top:4px}

/* footer */
.footer{left:74px;top:2991px;width:1049px;height:290px;background:linear-gradient(135deg,#0a8fd6,#16a6e9 50%,#0b93da);color:var(--white);overflow:hidden}
.footer .brand{left:84px;top:60px;width:190px;color:var(--white)}
.flink{font-size:14.5px;font-weight:600}
.fsocial{top:106px;width:40px;height:40px;border-radius:50%;border:1.5px solid var(--white);display:flex;align-items:center;justify-content:center;font-size:8px;font-weight:600}
.rule{left:38px;top:217px;width:973px;height:1px;background:rgba(255,255,255,.6)}
.copy{left:0;top:241px;width:1049px;text-align:center;font-size:14px;font-weight:500}
</style>
</head>
<body>

<header class="hero abs">
  <svg width="1049" height="587" viewBox="0 0 1049 587" aria-hidden="true">
    <defs>
      <linearGradient id="waveGrad" x1="0" y1="0" x2="1" y2="0">
        <stop offset="0" stop-color="#0a92d9"/>
        <stop offset=".5" stop-color="#0f9a8c"/>
        <stop offset="1" stop-color="#14882f"/>
      </linearGradient>
    </defs>
    <polygon points="0,381 256,419 358,470 479,508 689,419 1049,188 1049,587 0,587" fill="url(#waveGrad)"/>
  </svg>
  <div class="brand abs"><span class="mark"></span><span class="name">CORINNE HABBARD</span><span class="sub">CONSULTING</span></div>
  <nav>
    <a class="nav active abs" style="left:385px">HOME</a>
    <a class="nav abs" style="left:483px">ABOUT US</a>
    <a class="nav abs" style="left:612px">INSIGHTS</a>
    <a class="nav abs" style="left:734px">OUR SERVICES</a>
    <a class="nav abs" style="left:896px">CONTACT US</a>
  </nav>
  <h1 class="hero-title abs">CORINNE HABBARD <b>CONSULTING</b></h1>
  <p class="hero-text abs">We are starting a new consulting firm that will focus on<br>solving multiple industry problems with the mindset and<br>training of registered nurses.</p>
  <div class="hero-mark abs">CORINNE<br>HABBARD</div>
</header>

<h2 class="section-title abs" style="top:674px">OUR <b>SERVICES</b></h2>

<article class="service s-blue abs">
  <div class="icon"><svg width="40" height="40" viewBox="0 0 40 40" fill="none" stroke="#fff" stroke-width="2"><circle cx="20" cy="12" r="5"/><path d="M10 30c0-6 4-10 10-10s10 4 10 10"/><path d="M6 34h28"/></svg></div>
  <h3>LOREM IPSUM</h3>
  <p>Sed ut perspiciatis unde omnis<br>iste natus error sit voluptatem<br>accusantium doloremque</p>
  <div class="go"><svg width="28" height="28" viewBox="0 0 28 28"><path d="M12 9l5 5-5 5" fill="none" stroke="#0a9be0" stroke-width="2.5"/></svg></div>
</article>
<article class="service s-green abs">
  <div class="icon"><svg width="40" height="40" viewBox="0 0 40 40" fill="none" stroke="#fff" stroke-width="2"><circle cx="12" cy="12" r="4"/><circle cx="28" cy="12" r="4"/><path d="M5 28c0-5 3-9 7-9s7 4 7 9M21 28c0-5 3-9 7-9s7 4 7 9"/><path d="M4 32h32"/></svg></div>
  <h3>LOREM IPSUM</h3>
  <p>Sed ut perspiciatis unde omnis<br>iste natus error sit voluptatem<br>accusantium doloremque</p>
  <div class="go"><svg width="28" height="28" viewBox="0 0 28 28"><path d="M12 9l5 5-5 5" fill="none" stroke="#14902f" stroke-width="2.5"/></svg></div>
</article>
<article class="service s-orange abs">
  <div class="icon"><svg width="40" height="40" viewBox="0 0 40 40" fill="none" stroke="#fff" stroke-width="2"><rect x="10" y="6" width="24" height="18" rx="2"/><rect x="5" y="14" width="24" height="18" rx="2" fill="#f39200"/><circle cx="17" cy="23" r="4"/></svg></div>
  <h3>LOREM IPSUM</h3>
  <p>Sed ut perspiciatis unde omnis<br>iste natus error sit voluptatem<br>accusantium doloremque</p>
  <div class="go"><svg width="28" height="28" viewBox="0 0 28 28"><path d="M12 9l5 5-5 5" fill="none" stroke="#f39200" stroke-width="2.5"/></svg></div>
</article>
<article class="service s-red abs">
  <div class="icon"><svg width="40" height="40" viewBox="0 0 40 40" fill="none" stroke="#fff" stroke-width="2"><rect x="6" y="6" width="20" height="14" rx="1"/><path d="M16 20v5M8 27h16"/><circle cx="30" cy="22" r="4"/><path d="M24 34c0-4 3-6 6-6s6 2 6 6"/></svg></div>
  <h3>LOREM IPSUM</h3>
  <p>Sed ut perspiciatis unde omnis<br>iste natus error sit voluptatem<br>accusantium doloremque</p>
  <div class="go"><svg width="28" height="28" viewBox="0 0 28 28"><path d="M12 9l5 5-5 5" fill="none" stroke="#e30613" stroke-width="2.5"/></svg></div>
</article>

<a class="btn abs" style="left:483px;top:1202px;width:206px">VIEW SERVICES <svg width="20" height="10" viewBox="0 0 20 10"><path d="M0 5h18M14 1l4 4-4 4" fill="none" stroke="#fff" stroke-width="1.8"/></svg></a>

<section class="about abs">
  <svg class="abs" style="left:0;top:0" width="500" height="527" aria-hidden="true">
    <path d="M236 93 A165 165 0 1 1 90 343" fill="none" stroke="#fff" stroke-width="3"/>
    <circle cx="236" cy="256" r="150" fill="none" stroke="#fff" stroke-width="4"/>
  </svg>
  <div class="about-photo abs" role="img" aria-label="Photo of a seated audience attending a panel talk in a bright glass-walled room"></div>
  <h2 class="abs">ABOUT US</h2>
  <p class="abs">Lorem ipsum dolor sit amet, consectetur adipiscing elit, sed do<br>eiusmod tempor incididunt ut labore et dolore magna aliqua. Ut enim<br>ad minim veniam, quis nostrud exercitation ullamco laboris nisi ut<br>aliquip ex ea commodo consequat. Duis aute irure dolor in<br>reprehenderit in voluptate velit esse cillum dolore eu fugiat nulla<br>pariatur. Excepteur sint occaecat cupidatat non proident, sunt in<br>culpa qui officia deserunt mollit anim id est laborum.</p>
  <a class="btn light abs" style="left:507px;top:399px;width:177px">LEARN MORE <svg width="20" height="10" viewBox="0 0 20 10"><path d="M0 5h18M14 1l4 4-4 4" fill="none" stroke="#0a9be0" stroke-width="1.8"/></svg></a>
</section>

<h2 class="section-title abs" style="top:1959px">OUR <b>INSIGHTS</b></h2>

<article class="insight abs" style="left:74px">
  <span class="social">Linkpost</span><h4>LOREM IPSUM</h4><time>23RD FEB 2024</time>
  <p>Sed ut perspiciatis unde omnis iste natus<br>error sit voluptatem accusantium<br>doloremque laudantium</p>
</article>
<article class="insight abs" style="left:428px">
  <span class="social">Chirp</span><h4>LOREM IPSUM</h4><time>09TH MAR 2024</time>
  <p>Sed ut perspiciatis unde omnis iste natus<br>error sit voluptatem accusantium<br>doloremque laudantium</p>
</article>
<article class="insight abs" style="left:781px">
  <span class="social">Snapgram</span><h4>LOREM IPSUM</h4><time>06TH APR 2024</time>
  <p>Sed ut perspiciatis unde omnis iste natus<br>error sit voluptatem accusantium<br>doloremque laudantium</p>
</article>

<a class="btn abs" style="left:513px;top:2338px;width:172px">VIEW MORE <svg width="20" height="10" viewBox="0 0 20 10"><path d="M0 5h18M14 1l4 4-4 4" fill="none" stroke="#fff" stroke-width="1.8"/></svg></a>

<h2 class="section-title abs" style="top:2472px">CONTACT <b>US</b></h2>

<form>
  <div class="field abs" style="left:112px;top:2557px;width:455px">FIRST NAME<svg width="14" height="16" viewBox="0 0 14 16"><circle cx="7" cy="4.5" r="4"/><path d="M0 16c0-5 3-7 7-7s7 2 7 7z"/></svg></div>
  <div class="field abs" style="left:632px;top:2557px;width:455px">LAST NAME<svg width="14" height="16" viewBox="0 0 14 16"><circle cx="7" cy="4.5" r="4"/><path d="M0 16c0-5 3-7 7-7s7 2 7 7z"/></svg></div>
  <div class="field abs" style="left:112px;top:2646px;width:455px">EMAIL ADDRESS<svg width="18" height="13" viewBox="0 0 18 13"><rect x="1" y="1" width="16" height="11" fill="none" stroke="#1d1d1b" stroke-width="2"/><path d="M1 1l8 6 8-6" fill="none" stroke="#1d1d1b" stroke-width="2"/></svg></div>
  <div class="field abs" style="left:632px;top:2646px;width:455px">PHONE NUMBER<svg width="14" height="14" viewBox="0 0 14 14"><path d="M3 0l3 3-2 2c1 2 3 4 5 5l2-2 3 3-2 3C6 14 0 8 0 2z"/></svg></div>
  <div class="field abs" style="left:112px;top:2738px;width:975px;height:64px">MESSAGE<svg width="18" height="13" viewBox="0 0 18 13"><rect x="1" y="1" width="16" height="11" fill="none" stroke="#1d1d1b" stroke-width="2"/><path d="M1 1l8 6 8-6" fill="none" stroke="#1d1d1b" stroke-width="2"/></svg></div>
  <a class="btn abs" style="left:505px;top:2848px;width:188px">SUBMIT NOW <svg width="20" height="10" viewBox="0 0 20 10"><path d="M0 5h18M14 1l4 4-4 4" fill="none" stroke="#fff" stroke-width="1.8"/></svg></a>
</form>

<footer class="footer abs">
  <div class="brand abs"><span class="mark"></span><span class="name">CORINNE HABBARD</span><span class="sub">CONSULTING</span></div>
  <a class="flink abs" style="left:433px;top:63px">HOME</a>
  <a class="flink abs" style="left:433px;top:102px">ABOUT US</a>
  <a class="flink abs" style="left:433px;top:141px">INSIGHTS</a>
  <a class="flink abs" style="left:578px;top:63px">OUR SERVICES</a>
  <a class="flink abs" style="left:578px;top:102px">CONTACT US</a>
  <span class="fsocial abs" style="left:813px">Link</span>
  <span class="fsocial abs" style="left:866px">Chirp</span>
  <span class="fsocial abs" style="left:918px">Snap</span>
  <div class="rule abs"></div>
  <p class="copy abs">@2024 COPYRIGHTS - ALL RIGHTS RESERVED</p>
</footer>

</body>
</html>
```